body balm label design

body balm tube design, current label design for other similar products
Need to have a design which can interchange between 3 different solutions
Amber Tide (Lavender + Vanilla)
Copper Ridge (Eucalyptus + Mint)
Fern Hollow (Bergamot + Cedarwood)
Tube size:
2.5h x 3.25 w
Target Market(s)
natural, solution focused
Requirements
Must have
- relatable to existing brand designs, focus on features and benefits

```html
<!DOCTYPE html>
<html lang="en">
<head>
<meta charset="utf-8">
<title>Willowmere Natural Body Balm Labels</title>
<link rel="stylesheet" href="https://fonts.googleapis.com/css2?family=Cormorant+Garamond:wght@500;600&family=Montserrat:wght@400;600&family=Parisienne&display=swap">
<style>
  :root {
    --page-bg: #eef0f3;
    --label-bg: #ffffff;
    --ink: #5f6b68;
    --ink-soft: #8a9592;
    --sleep: #7d949c;
    --sleep-dark: #5d747d;
    --sleep-tint: #e6ecee;
    --less: #a7bf97;
    --less-dark: #7f9b6e;
    --less-tint: #eef3ea;
    --relief: #6b9e58;
    --relief-dark: #4f7f3f;
    --relief-tint: #e7f0e3;
  }
  * { box-sizing: border-box; margin: 0; padding: 0; }
  html, body { width: 720px; height: 1200px; overflow: hidden; }
  body {
    background: var(--page-bg);
    font-family: "Montserrat", sans-serif;
    color: var(--ink);
    display: flex;
    flex-direction: column;
    align-items: center;
    justify-content: center;
    gap: 40px;
  }
  .label {
    position: relative;
    width: 600px;
    height: 340px;
    background: var(--label-bg);
    box-shadow: 0 2px 10px rgba(0,0,0,0.06);
    overflow: hidden;
  }
  .label--sleep  { --accent: var(--sleep);  --accent-dark: var(--sleep-dark);  --accent-tint: var(--sleep-tint); }
  .label--less   { --accent: var(--less);   --accent-dark: var(--less-dark);   --accent-tint: var(--less-tint); }
  .label--relief { --accent: var(--relief); --accent-dark: var(--relief-dark); --accent-tint: var(--relief-tint); }

  .botanical {
    position: absolute; left: 0; top: 0; width: 290px; height: 340px;
    background: linear-gradient(135deg, #ffffff 0%, var(--accent-tint) 55%, #ffffff 100%);
  }
  .product-name, .scent, .band-text {
    position: absolute;
    writing-mode: vertical-rl;
    transform: rotate(180deg);
    text-align: center;
    white-space: nowrap;
  }
  .product-name {
    left: 240px; top: 20px; width: 52px; height: 300px;
    font-family: "Cormorant Garamond", serif;
    font-weight: 500; font-size: 28px; letter-spacing: 2px;
    color: var(--accent);
    line-height: 52px;
  }
  .band {
    position: absolute; left: 300px; top: 0; width: 64px; height: 340px;
    background: var(--accent);
  }
  .band-arch {
    position: absolute; left: 6px; top: 18px; width: 52px; height: 110px;
    border-radius: 26px 26px 0 0;
    border: 1px solid rgba(255,255,255,0.7);
    display: flex; flex-direction: column; align-items: center; justify-content: center; gap: 6px;
  }
  .brand-dot { width: 14px; height: 14px; border-radius: 50%; background: #ffffff; }
  .brand-name {
    font-family: "Montserrat", sans-serif; font-weight: 600; font-size: 6.5px;
    letter-spacing: 0.5px; color: #ffffff;
  }
  .band-text {
    left: 0; top: 140px; width: 64px; height: 160px;
    line-height: 64px;
    font-size: 8px; letter-spacing: 2.5px; font-weight: 600; color: #ffffff;
  }
  .net-weight {
    position: absolute; left: 0; bottom: 16px; width: 64px;
    text-align: center; font-size: 6.5px; letter-spacing: 0.5px; color: #ffffff;
  }
  .scent {
    left: 382px; top: 20px; width: 52px; height: 300px;
    font-family: "Parisienne", cursive; font-size: 28px;
    color: var(--accent-dark); line-height: 52px;
  }
  .details {
    position: absolute; left: 456px; top: 34px; width: 124px;
    font-size: 7px; line-height: 1.45; color: var(--ink-soft);
  }
  .details h3 {
    font-size: 7px; font-weight: 600; letter-spacing: 1px;
    color: var(--accent-dark); margin-bottom: 3px;
  }
  .details p { margin-bottom: 12px; }
  .social {
    position: absolute; left: 456px; bottom: 44px; display: flex; gap: 6px;
  }
  .social span { width: 12px; height: 12px; border-radius: 50%; background: var(--accent); display: block; }
  .web {
    position: absolute; left: 456px; bottom: 26px;
    font-size: 7px; letter-spacing: 0.5px; color: var(--ink-soft);
  }
</style>
</head>
<body>

  <section class="label label--sleep">
    <div class="botanical" role="img" aria-label="Fine line drawing of lavender sprigs and vanilla orchid flowers"></div>
    <h2 class="product-name">AMBER TIDE</h2>
    <div class="band">
      <div class="band-arch"><span class="brand-dot"></span><span class="brand-name">Willowmere</span></div>
      <p class="band-text">NATURAL BODY BALM</p>
      <p class="net-weight">NET WT 2.5 OZ</p>
    </div>
    <p class="scent">Lavender + Vanilla</p>
    <div class="details">
      <h3>DESCRIPTION</h3>
      <p>A rich plant butter balm that softens and soothes dry skin.</p>
      <h3>HOW TO USE</h3>
      <p>Warm a small amount between palms and massage into skin.</p>
      <h3>INGREDIENTS</h3>
      <p>Shea butter, coconut oil, beeswax, essential oils, vitamin E.</p>
    </div>
    <div class="social"><span></span><span></span><span></span></div>
    <p class="web">willowmere.co</p>
  </section>

  <section class="label label--less">
    <div class="botanical" role="img" aria-label="Fine line drawing of bergamot branches and cedar sprigs"></div>
    <h2 class="product-name">FERN HOLLOW</h2>
    <div class="band">
      <div class="band-arch"><span class="brand-dot"></span><span class="brand-name">Willowmere</span></div>
      <p class="band-text">NATURAL BODY BALM</p>
      <p class="net-weight">NET WT 2.5 OZ</p>
    </div>
    <p class="scent">Bergamot + Cedarwood</p>
    <div class="details">
      <h3>DESCRIPTION</h3>
      <p>A rich plant butter balm that softens and soothes dry skin.</p>
      <h3>HOW TO USE</h3>
      <p>Warm a small amount between palms and massage into skin.</p>
      <h3>INGREDIENTS</h3>
      <p>Shea butter, coconut oil, beeswax, essential oils, vitamin E.</p>
    </div>
    <div class="social"><span></span><span></span><span></span></div>
    <p class="web">willowmere.co</p>
  </section>

  <section class="label label--relief">
    <div class="botanical" role="img" aria-label="Fine line drawing of eucalyptus leaves and mint stems"></div>
    <h2 class="product-name">COPPER RIDGE</h2>
    <div class="band">
      <div class="band-arch"><span class="brand-dot"></span><span class="brand-name">Willowmere</span></div>
      <p class="band-text">NATURAL BODY BALM</p>
      <p class="net-weight">NET WT 2.5 OZ</p>
    </div>
    <p class="scent">Eucalyptus + Mint</p>
    <div class="details">
      <h3>DESCRIPTION</h3>
      <p>A rich plant butter balm that softens and soothes dry skin.</p>
      <h3>HOW TO USE</h3>
      <p>Warm a small amount between palms and massage into skin.</p>
      <h3>INGREDIENTS</h3>
      <p>Shea butter, coconut oil, beeswax, essential oils, vitamin E.</p>
    </div>
    <div class="social"><span></span><span></span><span></span></div>
    <p class="web">willowmere.co</p>
  </section>

</body>
</html>
```